Harrow Grading LLC business card design

Excavation company business cards

Contact Information for Business Card

Harrow Grading LLC cell phone 208-417-6290 office phone 208-319-4856 harrowgradingllc@maplecove.com Driveways, site prep, retaining walls, septic systems, rock delivery

Colors

Designer to choose colors to be used in the design.

```html
<!DOCTYPE html>
<html lang="en">
<head>
<meta charset="utf-8">
<title>Harrow Grading LLC – Business Card</title>
<link rel="stylesheet" href="https://fonts.googleapis.com/css2?family=Michroma&family=Montserrat:wght@400;500;800&display=swap">
<style>
  :root {
    --page-bg: #e2e2e2;
    --orange: #e8641a;
    --peach: #f8d9c8;
    --white: #ffffff;
    --charcoal: #4a4a4a;
    --charcoal-dark: #3a3a3a;
    --slate: #5e5e5e;
  }
  * { margin: 0; padding: 0; box-sizing: border-box; }
  html, body {
    width: 1200px; height: 800px; overflow: hidden;
    background: var(--page-bg);
    font-family: "Montserrat", sans-serif;
  }
  .sheet {
    position: relative; width: 1200px; height: 800px;
    display: flex; align-items: center; justify-content: center; gap: 40px;
  }
  .card {
    position: relative; width: 540px; height: 310px;
    border-radius: 18px; overflow: hidden;
    box-shadow: 0 10px 24px rgba(0,0,0,0.18);
  }
  /* Front */
  .card--front { background: var(--orange); }
  .front-art {
    position: absolute; inset: 0; width: 100%; height: 100%;
  }
  .front-info {
    position: absolute; left: 26px; top: 118px; color: var(--white);
  }
  .holder-name {
    font-family: "Michroma", sans-serif; font-size: 20px; letter-spacing: 1px;
    line-height: 1.1; white-space: nowrap;
  }
  .holder-title { font-size: 12px; font-weight: 500; margin: 2px 0 14px; }
  .contact-list { list-style: none; font-size: 11px; line-height: 1.7; }
  .contact-list li { display: flex; align-items: center; gap: 7px; white-space: nowrap; }
  .contact-icon { width: 11px; height: 11px; flex: none; }
  .edge-mark {
    position: absolute; left: 0; bottom: 44px; width: 10px; height: 26px;
    background: var(--white);
  }
  .brand {
    position: absolute; left: 332px; top: 140px;
    font-family: "Montserrat", sans-serif; font-weight: 800;
    color: var(--orange); font-size: 22px; line-height: 1.05;
    letter-spacing: 1px; text-transform: uppercase;
  }
  /* Back */
  .card--back { background: var(--slate); }
  .back-art { position: absolute; left: 70px; top: 48px; width: 400px; height: 170px; }
  .back-url {
    position: absolute; left: 0; right: 0; bottom: 42px; text-align: center;
    color: var(--white); font-size: 13px; font-weight: 500; letter-spacing: 6px;
    text-transform: uppercase;
  }
</style>
</head>
<body>
<main class="sheet">

  <section class="card card--front" aria-label="Card front">
    <svg class="front-art" viewBox="0 0 540 310" role="img" aria-label="Illustration of an excavator arm and mountain peaks in peach, white and charcoal">
      <defs>
        <linearGradient id="artTone" x1="0" y1="0" x2="1" y2="1">
          <stop offset="0" stop-color="#ffffff"/>
          <stop offset="0.55" stop-color="#f8d9c8"/>
          <stop offset="1" stop-color="#ffffff"/>
        </linearGradient>
      </defs>
      <polygon points="292,0 540,0 540,310 276,310 264,220 284,130" fill="#4a4a4a"/>
      <polygon points="304,0 540,0 540,310 288,310 276,220 296,130" fill="url(#artTone)"/>
    </svg>

    <div class="front-info">
      <h1 class="holder-name">DANIEL REYES</h1>
      <p class="holder-title">President</p>
      <ul class="contact-list">
        <li>
          <svg class="contact-icon" viewBox="0 0 12 12" aria-hidden="true"><path d="M2.5 1l2 2.3-1 1.2a6 6 0 0 0 4 4l1.2-1 2.3 2-1 1.5C5 11 1 7 1 2.2z" fill="#fff"/></svg>
          208-319-4856
        </li>
        <li>
          <svg class="contact-icon" viewBox="0 0 12 12" aria-hidden="true"><rect x="3" y="0.8" width="6" height="10.4" rx="1" fill="none" stroke="#fff" stroke-width="1.2"/></svg>
          208-417-6290
        </li>
        <li>
          <svg class="contact-icon" viewBox="0 0 12 12" aria-hidden="true"><rect x="0.8" y="2.5" width="10.4" height="7" fill="none" stroke="#fff" stroke-width="1.2"/><path d="M1 3l5 3.5L11 3" fill="none" stroke="#fff" stroke-width="1.2"/></svg>
          harrowgradingllc@maplecove.com
        </li>
        <li>
          <svg class="contact-icon" viewBox="0 0 12 12" aria-hidden="true"><circle cx="6" cy="6" r="5.2" fill="#fff"/></svg>
          harrowgradingllc.com
        </li>
      </ul>
    </div>

    <span class="edge-mark" aria-hidden="true"></span>
    <p class="brand">Harrow<br>Grading LLC</p>
  </section>

  <section class="card card--back" aria-label="Card back">
    <svg class="back-art" viewBox="0 0 400 170" role="img" aria-label="Embossed illustration of an excavator digging beneath mountain peaks">
      <defs>
        <linearGradient id="embossTone" x1="0" y1="0" x2="1" y2="1">
          <stop offset="0" stop-color="#3a3a3a"/>
          <stop offset="0.5" stop-color="#6e6e6e"/>
          <stop offset="1" stop-color="#3a3a3a"/>
        </linearGradient>
      </defs>
      <rect width="400" height="170" rx="8" fill="url(#embossTone)"/>
    </svg>
    <p class="back-url">www.harrowgradingllc.com</p>
  </section>

</main>
</body>
</html>
```